Podiatry clinic requires a modern revamp and editing of existing website.

I would like a fresh new look and updated information for my current business website. An easy to navigate site with prominent address and phone number for call to action. We are a podiatry clinic that focuses on general and sports podiatry.
I would like 4 pages; including Home page, About Us, Services & Contact.
www.brambleridgepodiatry.net

Target Market(s)

Active working professionals.

Industry/Entity Type

Medical

Coding

Coded - Design and coding required

Number of Pages Required

4 page

Font styles to use
Sans Serif

Colors
6b449b

Requirements
Must have
• A modern look with logo and active images; clean and uncluttered. Visible phone number and address for call to action.
• 4 pages - Home, About Us, Services, Contact.
• Home page - update address & service logos.
• About Us - update of personal information.
• Services - Revamp of existing page.
• Contact page to include Google map, email & phone number.
Nice to have
• Ability to add content easily; eg. a blog or adding video onto Home page.
• Link to Facebook page.

```html
<!DOCTYPE html>
<html lang="en">
<head>
<meta charset="utf-8">
<title>Bramble Ridge Podiatry</title>
<link href="https://fonts.googleapis.com/css2?family=Open+Sans:wght@400;600;700;800&display=swap" rel="stylesheet">
<style>
:root{
  --purple:#6b449b;
  --purple-dark:#4f2f7a;
  --purple-light:#7650a6;
  --orange:#f47b20;
  --green:#8dc63f;
  --ink:#333;
  --muted:#777;
  --grey-bg:#f2f2f2;
  --white:#fff;
}
*{margin:0;padding:0;box-sizing:border-box}
html,body{width:1200px;height:3716px;overflow:hidden}
body{font-family:"Open Sans",Arial,sans-serif;color:var(--ink);background:var(--white);position:relative}
.abs{position:absolute}
p{font-size:13px;line-height:21px;color:var(--muted)}
.btn{display:inline-block;color:var(--white);font-size:12px;font-weight:700;text-transform:uppercase;padding:11px 24px;letter-spacing:.5px}
.btn-orange{background:var(--orange)}
.btn-green{background:var(--green)}
.section-title{position:absolute;left:0;width:1200px;text-align:center;color:var(--purple);font-size:30px;font-weight:800;text-transform:uppercase}

/* header */
.header-bg{left:0;top:0;width:1200px;height:640px}
.brand{left:160px;top:34px;display:flex;align-items:center;gap:10px;color:var(--white);font-weight:800;font-size:20px;white-space:nowrap}
.brand-mark{width:34px;height:34px;background:var(--orange);border-radius:50%;flex:none}
.topbar{left:560px;top:22px;color:#e6dcf2;font-size:12px;display:flex;gap:28px}
.nav{left:580px;top:66px;display:flex}
.nav a{color:var(--white);font-size:13px;font-weight:700;padding:20px 16px;text-decoration:none;text-transform:uppercase}
.nav a.active{background:var(--orange)}
.hero{left:160px;top:140px;width:880px;height:480px;background:linear-gradient(110deg,#2b2230 0%,#5a4550 45%,#c98a55 75%,#e9b47a 100%)}
.hero-title{left:200px;top:250px;font-size:62px;line-height:68px;font-weight:800;color:var(--white);text-transform:uppercase}
.hero-title span{color:var(--orange)}
.hero-btn{left:200px;top:470px}
.dots{left:940px;top:585px;display:flex;gap:8px}
.dots i{width:10px;height:10px;border-radius:50%;background:rgba(255,255,255,.6)}
.dots i:first-child{background:var(--white)}

/* welcome */
.welcome-img{left:160px;top:745px;width:420px;height:355px;background:linear-gradient(160deg,#8e6a5a,#d9a88c 55%,#f0d5c4)}
.welcome-text{left:610px;top:760px;width:430px}
.welcome-text p{margin-bottom:16px}

/* cta band */
.cta{left:0;top:1160px;width:1200px;height:220px;background:var(--green);text-align:center;color:var(--white)}
.cta h3{margin-top:40px;font-size:22px;font-weight:700;text-transform:uppercase}
.cta .lines{margin-top:18px;font-size:28px;font-weight:600;display:flex;justify-content:center;align-items:center;gap:16px}
.cta .btn{margin-top:22px}

/* about */
.about-photo{left:180px;top:1480px;width:200px;height:210px;background:linear-gradient(180deg,#dfe9ef,#b8cbd6)}
.about-text{left:440px;top:1475px;width:600px}
.about-text .role{font-size:14px;font-weight:700;color:var(--ink)}
.about-text .name{font-size:30px;color:var(--orange);margin:6px 0 4px}
.about-text .cred{font-size:13px;font-weight:700;color:var(--ink);margin-bottom:18px}
.about-text p{margin-bottom:16px}

/* purple band */
.info-band{left:0;top:1880px;width:1200px;height:300px;background:var(--purple)}
.info-col{position:absolute;top:50px;width:260px;display:flex;gap:14px}
.info-col p{color:#e4dbef}
.info-col svg{flex:none}
.info-band .btn{position:absolute;left:400px;top:205px;width:400px;text-align:center;font-size:11px;white-space:nowrap}

/* partners */
.partners{left:190px;top:2245px;width:820px;display:flex;justify-content:space-between;align-items:center}
.badge{height:60px;border-radius:4px}

/* services */
.services{left:0;top:2380px;width:1200px;height:840px;background:var(--grey-bg)}
.service{position:absolute;width:400px}
.service .thumb{width:112px;height:112px}
.service h4{position:absolute;left:138px;top:18px;color:var(--purple);font-size:26px;line-height:30px;font-weight:800;text-transform:uppercase}
.service p{margin-top:30px}
.service .btn{margin-top:22px;padding:9px 20px;font-size:11px}

/* footer */
.footer-bg{left:0;top:3200px;width:1200px;height:516px}
.footer-col{position:absolute;top:3440px;color:#e4dbef;font-size:12px;line-height:22px}
.footer-col h5{color:var(--white);font-size:14px;margin-bottom:10px}
.footer-brand{left:160px;top:3432px;font-size:16px}
.footer-brand .brand-mark{width:28px;height:28px}
.map{width:170px;height:110px;background:linear-gradient(135deg,#e8e8e8,#cfd8cf)}
.copyright{left:0;top:3670px;width:1200px;height:46px;background:var(--purple-dark);color:#cbbde0;font-size:12px;text-align:center;line-height:46px}
</style>
</head>
<body>

<svg class="abs header-bg" viewBox="0 0 1200 640" aria-hidden="true">
  <rect width="1200" height="640" fill="#6b449b"/>
  <polygon points="700,0 1200,0 1200,640 1000,640" fill="#7650a6"/>
  <polygon points="0,420 160,560 160,640 0,640" fill="#fff"/>
  <polygon points="1040,560 1200,400 1200,640 1040,640" fill="#fff"/>
</svg>

<div class="abs brand"><span class="brand-mark"></span>Bramble Ridge Podiatry</div>
<div class="abs topbar"><span>✉ info@brambleridgepodiatry.net</span><span>☎ 1300 555 016 | 12 Larch Street, Ridgeview</span></div>
<nav class="abs nav"><a class="active">Home</a><a>About Us</a><a>Podiatry Services</a><a>Contact</a></nav>

<div class="abs hero" role="img" aria-label="Runner's feet striding along a sunlit road"></div>
<div class="abs hero-title">Bramble<br><span>Ridge</span><br>Podiatry</div>
<a class="abs btn btn-orange hero-btn">Learn More</a>
<div class="abs dots"><i></i><i></i><i></i><i></i></div>

<h2 class="section-title" style="top:672px">Welcome to Bramble Ridge Podiatry</h2>
<div class="abs welcome-img" role="img" aria-label="Close view of a bare foot being examined"></div>
<div class="abs welcome-text">
  <p>Bramble Ridge Podiatry is a friendly clinic in the heart of the valley, helping local families and active workers stay on their feet. Our team of qualified podiatrists offers careful assessment and practical care.</p>
  <p>We provide general podiatry treatment and sports care for people of all ages, including orthotics, footwear advice, nail care and ongoing management plans that fit busy lives.</p>
</div>

<section class="abs cta">
  <h3>For Appointments or Enquiries</h3>
  <div class="lines">
    <svg width="26" height="26" viewBox="0 0 24 24" aria-hidden="true"><path fill="#fff" d="M6.6 10.8a15 15 0 0 0 6.6 6.6l2.2-2.2c.3-.3.7-.4 1-.2 1.1.4 2.3.6 3.6.6.6 0 1 .4 1 1V20c0 .6-.4 1-1 1A17 17 0 0 1 3 4c0-.6.4-1 1-1h3.5c.6 0 1 .4 1 1 0 1.3.2 2.5.6 3.6.1.3 0 .7-.2 1z"/></svg>
    <span>1300 555 016</span><span>|</span>
    <svg width="26" height="26" viewBox="0 0 24 24" aria-hidden="true"><path fill="#fff" d="M12 2a10 10 0 1 0 5 18.7l-.9-1.7A8 8 0 1 1 20 12v1a2 2 0 0 1-4 0V7h-2v1a5 5 0 1 0 1 7 4 4 0 0 0 7-2v-1A10 10 0 0 0 12 2zm0 13a3 3 0 1 1 0-6 3 3 0 0 1 0 6z"/></svg>
    <span>info@brambleridgepodiatry.net</span>
  </div>
  <a class="btn btn-orange">Contact Us</a>
</section>

<h2 class="section-title" style="top:1420px">About Us</h2>
<div class="abs about-photo" role="img" aria-label="Portrait of the clinic's chief podiatrist in a white coat"></div>
<div class="abs about-text">
  <div class="role">Director / Chief Podiatrist</div>
  <div class="name">Clara Benton</div>
  <div class="cred">B.POD. (HONS) M.CLIN.POD.</div>
  <p>Clara studied podiatry at university and has worked in private practice across the region for many years. She holds a master's degree in clinical podiatry and a keen interest in sports injuries and running gait.</p>
  <p>Clara has worked with community teams and local athletes, and she enjoys helping people return to the activities they love with confidence and less pain.</p>
  <p>Outside the clinic Clara keeps active with trail running and cycling, and she brings that same energy to every consultation at Bramble Ridge Podiatry.</p>
</div>

<section class="abs info-band">
  <div class="info-col" style="left:180px">
    <svg width="26" height="26" viewBox="0 0 24 24" aria-hidden="true"><circle cx="12" cy="12" r="11" fill="#fff"/><path d="M7 12.5l3.2 3.2L17 9" stroke="#6b449b" stroke-width="2.4" fill="none"/></svg>
    <p>Payments are accepted via cash, EFTPOS or credit card at the time of your visit.</p>
  </div>
  <div class="info-col" style="left:480px">
    <svg width="26" height="26" viewBox="0 0 24 24" aria-hidden="true"><circle cx="12" cy="12" r="11" fill="#fff"/><path d="M7 12.5l3.2 3.2L17 9" stroke="#6b449b" stroke-width="2.4" fill="none"/></svg>
    <p>Instant health fund claiming is available on the spot. Check your extras cover for eligibility and rebate amounts.</p>
  </div>
  <div class="info-col" style="left:780px">
    <svg width="26" height="26" viewBox="0 0 24 24" aria-hidden="true"><circle cx="12" cy="12" r="11" fill="#fff"/><path d="M7 12.5l3.2 3.2L17 9" stroke="#6b449b" stroke-width="2.4" fill="none"/></svg>
    <p>Government rebates are available for eligible patients under a GP care plan arrangement.</p>
  </div>
  <a class="btn btn-orange">Please contact our clinic for more information</a>
</section>

<div class="abs partners" aria-label="Partner and accreditation badges">
  <div class="badge" style="width:160px;background:#e9e3f1"></div>
  <div class="badge" style="width:170px;background:#ececec"></div>
  <div class="badge" style="width:150px;background:#dde6f3"></div>
  <div class="badge" style="width:140px;background:#cde5c0"></div>
</div>

<section class="abs services">
  <h2 class="section-title" style="top:60px">Podiatry Services</h2>

  <div class="service" style="left:180px;top:150px">
    <div class="thumb" role="img" aria-label="Feet resting on a clinic floor" style="background:linear-gradient(135deg,#b88a70,#e8c3a8)"></div>
    <h4>Diabetic<br>Management</h4>
    <p>Regular foot checks help people with diabetes avoid serious problems. We assess circulation and sensation, and give clear advice on daily care and footwear.</p>
    <a class="btn btn-green">Read More</a>
  </div>
  <div class="service" style="left:620px;top:150px">
    <div class="thumb" role="img" aria-label="Toenail being treated by a podiatrist" style="background:linear-gradient(135deg,#9c6f60,#dcb49c)"></div>
    <h4>Nail<br>Surgery</h4>
    <p>Painful ingrown toenails can be treated with a simple procedure under local anaesthetic. Most patients walk out comfortably and recover within days.</p>
    <a class="btn btn-green">Read More</a>
  </div>
  <div class="service" style="left:180px;top:540px">
    <div class="thumb" role="img" aria-label="Foot on a pressure assessment plate" style="background:linear-gradient(135deg,#6f8fb3,#c6d6e6)"></div>
    <h4>Bio Mechanical<br>Assessment</h4>
    <p>We study how your feet, legs and hips move together. Findings guide treatment such as exercises, footwear changes or custom orthotics.</p>
    <a class="btn btn-green">Read More</a>
  </div>
  <div class="service" style="left:620px;top:540px">
    <div class="thumb" role="img" aria-label="Runner's legs mid stride on a track" style="background:linear-gradient(135deg,#7a6a5e,#c9b29c)"></div>
    <h4>Gait<br>Analysis</h4>
    <p>Video gait analysis shows how you walk and run. It helps find the cause of recurring pain and improves comfort for training and work.</p>
    <a class="btn btn-green">Read More</a>
  </div>
</section>

<svg class="abs footer-bg" viewBox="0 0 1200 516" aria-hidden="true">
  <polygon points="0,60 1200,0 1200,516 0,516" fill="#6b449b"/>
  <polygon points="0,60 500,35 0,200" fill="#7650a6"/>
</svg>
<div class="abs brand footer-brand"><span class="brand-mark"></span>Bramble Ridge Podiatry</div>
<div class="footer-col" style="left:480px"><h5>Quick Links</h5>Home<br>About Us<br>Podiatry Services<br>Contact Us</div>
<div class="footer-col" style="left:650px"><h5>Bramble Ridge Podiatry</h5>12 Larch Street<br>Ridgeview VIC 3999<br><br>Phone: 1300 555 016<br>Email: info@brambleridgepodiatry.net</div>
<div class="footer-col" style="left:890px"><h5>Location</h5><div class="map" role="img" aria-label="Street map showing the clinic location"></div></div>
<div class="abs copyright">© 2024 Bramble Ridge Podiatry. All Rights Reserved.</div>

</body>
</html>
```